Marlow Sail Works President Business Card Carbon fiber catamarans

Hi.. I need a new business card design.. I am the President of a high tech yacht builder. We build Carbon Fiber go fast catamarans... Maybe we use the file I am sharing to you as the back of the card.. We need to look cool and crisp ...

Target Market(s)

Affluent People who will purchase a cool yacht

Industry/Entity Type

Custom Yacht Builder

Contact Information for Business Card

Dean Pellway , President, 731.508.2164 USA

Font styles to use
Serif

Requirements
Must have
• the clean crisp cool feel
Nice to have
• clean and crisp
Should not have
• Bold ugly

```html
<!DOCTYPE html>
<html lang="en">
<head>
<meta charset="utf-8">
<title>Marlow Sail Works – Business Card</title>
<link href="https://fonts.googleapis.com/css2?family=Roboto:wght@400;500&display=swap" rel="stylesheet">
<style>
  :root {
    --page-bg: #e4e4e4;
    --card-white: #ffffff;
    --ink-dark: #1e1e1e;
    --ink-mid: #555555;
    --divider: #cfcfcf;
    --brand-grey: #5a5a5a;
    --back-dark: #1b1b1b;
    --back-mid: #262626;
    --back-brand: #333333;
  }
  * { margin: 0; padding: 0; box-sizing: border-box; }
  html, body {
    width: 1200px; height: 1200px; overflow: hidden;
    background: var(--page-bg);
    font-family: 'Roboto', Arial, sans-serif;
  }
  .card {
    position: absolute;
    left: 262px; width: 686px; height: 392px;
    border-radius: 19px;
    overflow: hidden;
  }
  .card-front { top: 165px; background: var(--card-white); }
  .card-back { top: 653px; background: var(--back-dark); }

  .brand-lockup {
    position: absolute; left: 62px; top: 156px;
    display: flex; align-items: center; gap: 12px;
  }
  .brand-dot {
    width: 50px; height: 50px; border-radius: 50%;
    background: var(--brand-grey);
  }
  .brand-name {
    color: var(--brand-grey);
    font-weight: 400;
    font-size: 25px;
    letter-spacing: 3px;
    line-height: 1.1;
    text-transform: uppercase;
  }

  .divider {
    position: absolute; left: 346px; top: 92px;
    width: 1px; height: 235px; background: var(--divider);
  }

  .contact-block {
    position: absolute; left: 369px; top: 97px;
    color: var(--ink-mid);
  }
  .person-name {
    font-size: 22px; font-weight: 500; color: var(--ink-dark);
    letter-spacing: 0.5px; line-height: 1.2;
  }
  .person-title { font-size: 15px; font-weight: 500; margin-top: 2px; }
  .address { font-size: 15px; line-height: 19px; margin-top: 18px; }
  .contact-list { list-style: none; margin-top: 15px; font-size: 15px; }
  .contact-list li { display: flex; align-items: center; height: 19.3px; }
  .contact-list svg { width: 12px; height: 12px; margin-right: 10px; fill: var(--ink-dark); }

  .back-surface {
    position: absolute; inset: 0;
    background: radial-gradient(ellipse at 50% 45%, var(--back-mid), var(--back-dark) 75%);
  }
  .back-brand {
    position: absolute; left: 0; right: 0; top: 150px;
    text-align: center;
    color: var(--back-brand);
    font-weight: 400; font-size: 44px;
    letter-spacing: 6px; text-transform: uppercase;
  }
</style>
</head>
<body>

<section class="card card-front">
  <div class="brand-lockup">
    <span class="brand-dot"></span>
    <span class="brand-name">Marlow<br>Sail Works</span>
  </div>

  <div class="divider"></div>

  <div class="contact-block">
    <div class="person-name">DEAN PELLWAY</div>
    <div class="person-title">President</div>
    <div class="address">2140 Harbor Crest Road<br>Newport, Rhode Island 02840</div>
    <ul class="contact-list">
      <li><svg viewBox="0 0 24 24"><path d="M6.6 10.8a15.1 15.1 0 0 0 6.6 6.6l2.2-2.2a1 1 0 0 1 1-.25 11.4 11.4 0 0 0 3.6.57 1 1 0 0 1 1 1V20a1 1 0 0 1-1 1A17 17 0 0 1 3 4a1 1 0 0 1 1-1h3.5a1 1 0 0 1 1 1c0 1.25.2 2.45.57 3.6a1 1 0 0 1-.25 1z"/></svg>731-508-2164</li>
      <li><svg viewBox="0 0 24 24"><path d="M7 1h10a2 2 0 0 1 2 2v18a2 2 0 0 1-2 2H7a2 2 0 0 1-2-2V3a2 2 0 0 1 2-2zm0 3v15h10V4z"/></svg>731-508-2190</li>
      <li><svg viewBox="0 0 24 24"><path d="M6 2h12v6H6zM3 9h18a2 2 0 0 1 2 2v7h-4v4H5v-4H1v-7a2 2 0 0 1 2-2zm4 8v3h10v-3z"/></svg>731-508-2177</li>
      <li><svg viewBox="0 0 24 24"><path d="M2 5h20v14H2zm2 2v.5l8 5 8-5V7z"/></svg>name@marlowsail.com</li>
      <li><svg viewBox="0 0 24 24"><circle cx="12" cy="12" r="10"/></svg>www.marlowsail.com</li>
    </ul>
  </div>
</section>

<section class="card card-back">
  <div class="back-surface" role="img" aria-label="Dark perforated carbon texture across the card back"></div>
  <div class="back-brand">Marlow Sail Works</div>
</section>

</body>
</html>
```